Real Estate Website

I am looking for a website design for a website that will be featuring real estate listings across Australia. It will be a website for a real estate agency that operates through all states in Australia.

We like the designs of https://www.brightnest.com.au/ and https://valtoria.example/

On the brightnest website, we like the sell, buy, sold tabs but would also like lease, and agents. We also need a button somewhere for 'Join Agent Pivola' and 'Login'

On the Valtoria site it has a concierge section and we want something like that on the home page.

The contact details to show in the footer are:

Shop 2217B
Level 1 Harbourgate Shopping Centre
87 Quillon Terrace
Southport

Attached are various versions of the logo and some intro text to go on the home page.

```html
<!DOCTYPE html>
<html lang="en">
<head>
<meta charset="utf-8">
<title>Agent Pivola — Real Estate Across Australia</title>
<link href="https://fonts.googleapis.com/css2?family=Montserrat:wght@400;500;600;700&family=Lato:wght@400;700&display=swap" rel="stylesheet">
<style>
:root{
  --gold:#b08a48;
  --gold-band:#ad8541;
  --gold-btn:#d9bf6e;
  --ink:#1b1b1b;
  --text:#444;
  --muted:#8a8a8a;
  --light:#f8f7f5;
  --footer:#1f1f1f;
  --white:#fff;
}
*{box-sizing:border-box;margin:0;padding:0}
html,body{width:1200px;height:3807px;overflow:hidden}
body{position:relative;font-family:"Lato",sans-serif;color:var(--text);background:var(--white)}
.abs{position:absolute}
.heading{font-family:"Montserrat",sans-serif;font-weight:600;font-size:35px;color:var(--ink);text-align:center;width:1200px;left:0;letter-spacing:.5px}
.heading span{color:var(--gold)}

/* hero */
.hero{left:0;top:0;width:1200px;height:643px;background:linear-gradient(180deg,#5a5f86 0%,#a9707a 20%,#c48a6a 30%,#3b4660 55%,#2a3244 80%,#3a4356 100%)}
.notch{left:540px;top:600px;width:120px;height:60px}
.logo{left:112px;top:60px;width:150px;display:flex;align-items:center;gap:8px;color:var(--white);font-family:"Montserrat",sans-serif;font-weight:600;font-size:15px;letter-spacing:2px;text-transform:uppercase}
.logo i{width:12px;height:12px;border-radius:50%;background:var(--white);display:block}
.nav{left:354px;top:60px;display:flex;gap:40px;font-family:"Montserrat",sans-serif;font-weight:500;font-size:14px;color:var(--white);text-transform:uppercase}
.nav .active{color:#f1d37a}
.nav .caret::after{content:"";display:inline-block;margin-left:6px;border:4px solid transparent;border-top-color:#fff;vertical-align:-1px}
.join{left:927px;top:46px;width:184px;height:43px;border-radius:6px;background:var(--white);color:var(--gold);font-family:"Montserrat",sans-serif;font-weight:600;font-size:14px;display:flex;align-items:center;justify-content:center;text-transform:uppercase}
.hero-title{left:0;top:195px;width:1200px;text-align:center;font-family:"Montserrat",sans-serif;font-weight:500;font-size:118px;letter-spacing:24px;color:var(--white);line-height:1}
.tabs{left:210px;top:364px;display:flex;gap:26px;font-family:"Montserrat",sans-serif;font-weight:500;font-size:14px;color:var(--white)}
.search{left:186px;top:402px;width:828px;height:65px;background:var(--white);border-radius:5px}
.search p{position:absolute;left:30px;top:23px;font-size:14px;color:#9a9a9a}
.search b{position:absolute;right:6px;top:5px;width:250px;height:55px;border-radius:4px;background:linear-gradient(180deg,#e6cf82,#c9a653);font-family:"Montserrat",sans-serif;font-weight:600;font-size:14px;color:#2a2212;display:flex;align-items:center;justify-content:center}

/* category tiles */
.tile{top:724px;width:316px;height:321px;display:flex;align-items:center;justify-content:center;font-family:"Montserrat",sans-serif;font-weight:600;font-size:24px;color:var(--white)}
.tile.buy{left:111px;background:linear-gradient(180deg,#7c8391,#6a6158 60%,#4a5a3a)}
.tile.sell{left:442px;background:linear-gradient(180deg,#6f7f95,#8a8676 55%,#5f7a3a)}
.tile.lease{left:773px;background:linear-gradient(180deg,#7f95ad,#b9b6ae 55%,#6e7e55)}

/* featured */
.featured{left:0;top:1128px;width:1200px;height:634px;background:var(--light)}
.listing{top:1280px;width:370px;height:331px;background:var(--white);box-shadow:0 3px 10px rgba(0,0,0,.08)}
.listing .photo{height:238px}
.listing h3{font-weight:400;font-size:16px;color:var(--ink);text-align:center;margin-top:20px}
.listing .meta{display:flex;justify-content:center;gap:8px;margin-top:16px;font-size:14px;color:#666}
.listing .meta span::before{content:"";display:inline-block;width:14px;height:9px;background:#999;border-radius:2px;margin-right:7px}
.dots{left:551px;top:1676px;display:flex;gap:8px;align-items:center}
.dots i{display:block;width:10px;height:10px;border-radius:5px;background:#c9ae77}
.dots i.on{width:54px}

/* about */
.about{left:0;top:1762px;width:1200px;height:504px;background:var(--gold-band)}
.about .photo{left:109px;top:1840px;width:417px;height:347px;border:3px solid var(--white);border-radius:14px;background:linear-gradient(135deg,#d7cfc4,#e4c2a0 45%,#4d6b8a)}
.about h2{left:596px;top:1845px;font-family:"Montserrat",sans-serif;font-weight:600;font-size:35px;color:var(--white)}
.about .copy{left:599px;top:1897px;width:488px;font-family:"Montserrat",sans-serif;font-size:14px;line-height:26px;color:var(--white);text-align:justify}
.about .copy p+p{margin-top:24px}
.btn-white{background:var(--white);color:var(--gold);font-family:"Montserrat",sans-serif;font-weight:600;font-size:14px;border-radius:4px;display:flex;align-items:center;justify-content:center;text-transform:uppercase}
.about .btn-white{left:599px;top:2125px;width:136px;height:45px}

/* concierge */
.concierge{left:111px;top:2431px;width:978px;height:312px;border-radius:6px;background:linear-gradient(90deg,#2d3a52,#3c4a63 35%,#2a3650 65%,#3b3a48)}
.concierge .lead{left:133px;top:2470px;width:450px;text-align:center;font-family:"Lato",sans-serif;font-size:27px;line-height:43px;color:var(--white)}
.concierge-text{left:610px;top:2472px;width:450px;text-align:center;font-size:20px;line-height:33px;color:var(--white)}
.concierge-btn{left:514px;top:2647px;width:172px;height:45px}

/* testimonials */
.review{width:311px;height:340px;background:var(--white);padding:40px 18px 0;font-size:16px;line-height:27px;color:#333}
.review.boxed{border:1px solid #ddd;top:2903px}
.review.lift{top:2941px;box-shadow:0 4px 16px rgba(0,0,0,.09)}
.stars{color:#f5b21b;font-size:19px;letter-spacing:1px;margin-bottom:12px}
.review h4{font-family:"Montserrat",sans-serif;font-weight:700;font-size:16px;color:var(--ink);margin-top:32px;line-height:20px}
.review h4.gold{color:var(--gold)}
.review small{display:block;font-size:14px;color:var(--muted);line-height:20px}
.review small.gold{color:var(--gold)}

/* footer */
.footer{left:0;top:3374px;width:1200px;height:433px;background:var(--footer)}
.f-head{top:3443px;font-family:"Montserrat",sans-serif;font-weight:600;font-size:16px;color:var(--white)}
.links{left:111px;top:3488px;list-style:none;font-size:12px;color:var(--white)}
.links li{height:33px}
.links li::before{content:"»";margin-right:12px}
.contact{left:321px;top:3486px;color:var(--white);font-size:12px;line-height:18px}
.contact .row{display:flex;gap:18px;align-items:center;margin-bottom:14px}
.contact .ico{width:36px;height:36px;border:2px solid var(--white);border-radius:50%;display:flex;align-items:center;justify-content:center;flex:none}
.field{background:var(--white);border:1px solid #bbb;font-size:11px;color:#888;padding:8px 10px}
.submit{left:1004px;top:3663px;width:84px;height:31px;background:#f1d37a;color:#1b1b1b;font-family:"Montserrat",sans-serif;font-weight:600;font-size:12px;display:flex;align-items:center;justify-content:center}
.rule{left:96px;top:3714px;width:1008px;height:1px;background:#444}
.copyright{left:111px;top:3741px;font-size:12px;color:var(--white)}
.social{left:942px;top:3733px;display:flex;gap:10px}
.social i{width:30px;height:30px;border:1.5px solid var(--white);border-radius:50%;display:block}
.social i.hl{background:#f1d37a;border-color:#f1d37a}
</style>
</head>
<body>

<!-- hero -->
<div class="abs hero" role="img" aria-label="City skyline at sunset over a river"></div>
<svg class="abs notch" viewBox="0 0 120 60"><path d="M0 43 C30 43 35 5 60 5 C85 5 90 43 120 43 L120 60 L0 60Z" fill="#fff"/><rect x="50" y="18" width="20" height="32" rx="10" fill="none" stroke="#888" stroke-width="2"/><path d="M60 26 V40 M55 35 L60 40 L65 35" stroke="#888" stroke-width="2" fill="none"/></svg>
<div class="abs logo"><i></i>Agent Pivola</div>
<nav class="abs nav">
  <span class="active">Home</span><span class="caret">Sell</span><span class="caret">Buy</span><span>About</span><span>Members</span><span>Contact Us</span>
</nav>
<div class="abs join">Join Agent Pivola</div>
<h1 class="abs hero-title">AGENT PIVOLA</h1>
<div class="abs tabs"><span>Sell</span><span>Buy</span><span>Sold</span><span>Lease</span><span>Agents</span></div>
<div class="abs search"><p>Start typing to find your address</p><b>GET PROPERTY ESTIMATE</b></div>

<!-- categories -->
<div class="abs tile buy" role="img" aria-label="Apartment buildings along a paved path">Buy</div>
<div class="abs tile sell" role="img" aria-label="Suburban two-storey house with lawn">Sell</div>
<div class="abs tile lease" role="img" aria-label="Modern apartment blocks with a walkway">Lease</div>

<!-- featured listings -->
<div class="abs featured"></div>
<h2 class="abs heading" style="top:1203px">FEATURED <span>LISTINGS</span></h2>
<article class="abs listing" style="left:30px"><div class="photo" role="img" aria-label="White kitchen with pendant lights" style="background:linear-gradient(135deg,#eceae6,#cfc8bd 60%,#2c3550)"></div><h3>Excepteur sint occaecat cupidatat</h3><div class="meta"><span>5 Beds |</span><span>3 Baths |</span><span>16 Guests</span></div></article>
<article class="abs listing" style="left:415px"><div class="photo" role="img" aria-label="Grey weatherboard house with front garden" style="background:linear-gradient(180deg,#6d8fb8,#8a8c92 50%,#4f7a2f)"></div><h3>Excepteur sint occaecat cupidatat</h3><div class="meta"><span>5 Beds |</span><span>3 Baths |</span><span>16 Guests</span></div></article>
<article class="abs listing" style="left:800px"><div class="photo" role="img" aria-label="Bright living room with timber floor" style="background:linear-gradient(180deg,#f0efec,#d8d4ce 60%,#8a5a35)"></div><h3>Excepteur sint occaecat cupidatat</h3><div class="meta"><span>5 Beds |</span><span>3 Baths |</span><span>16 Guests</span></div></article>
<div class="abs dots"><i></i><i></i><i class="on"></i></div>

<!-- about -->
<section class="abs about"></section>
<div class="abs photo about" style="position:absolute;left:109px;top:1840px;width:417px;height:347px;border:3px solid #fff;border-radius:14px;background:linear-gradient(135deg,#d7cfc4,#e4c2a0 45%,#4d6b8a)" role="img" aria-label="Smiling family of three hugging"></div>
<h2 class="abs" style="left:596px;top:1845px;font-family:'Montserrat',sans-serif;font-weight:600;font-size:35px;color:#fff">ABOUT AGENT PIVOLA</h2>
<div class="abs" style="left:599px;top:1897px;width:488px;font-family:'Montserrat',sans-serif;font-size:14px;line-height:26px;color:#fff;text-align:justify">
  <p>Lorem ipsum dolor sit amet, consectetur adipiscing elit, sed do eiusmod tempor incididunt ut labore et dolore magna aliqua. Ut enim ad minim veniam, quis nostrud exercitation ullamco laboris nisi ut aliquip ex ea commodo consequat.</p>
  <p style="margin-top:24px">Duis aute irure dolor in reprehenderit in voluptate velit esse cillum dolore eu fugiat nulla pariatur. Excepteur sint occaecat cupidatat non proident, sunt in culpa qui officia deserunt mollit anim id est laborum.</p>
</div>
<div class="abs btn-white" style="left:599px;top:2125px;width:136px;height:45px">Read More</div>

<!-- concierge -->
<h2 class="abs heading" style="top:2345px">AGENT PIVOLA <span>CONCIERGE</span></h2>
<div class="abs concierge" role="img" aria-label="Coastal high-rise apartments at dusk"></div>
<p class="abs" style="left:133px;top:2470px;width:450px;text-align:center;font-size:27px;line-height:43px;color:#fff">Looking buy, rent or sell something unique? Want competitive developer financing at great rates?</p>
<p class="abs concierge-text">Concierge can help you find, buy, rent or sell unique properties through our extensive global agent network and assist with financing at competitive rates with fast approvals.</p>
<div class="abs btn-white concierge-btn">Find Out More</div>

<!-- testimonials -->
<h2 class="abs heading" style="top:2814px">WHAT OUR <span>CUSTOMER SAYS</span></h2>
<div class="abs review boxed" style="left:109px"><div class="stars">★★★★★</div>“Tallowby Cottage was a great place to stay in a very convenient location. Check in was easy, communication with Maren &amp; Tobias was fast and clear and the house was great for our young family. Thoroughly recommended.”<h4>Elsie Marrow</h4><small>United States</small></div>
<div class="abs review lift" style="left:451px"><div class="stars">★★★★★</div>“Corrawin Ridge Villa is beautiful and very well- appointed, with lots of stylish touches. It’s the perfect place to relax and unwind, and is in a great location. We had a lovely weekend there - highly recommended.<h4 class="gold">Priya Lindqvist</h4><small class="gold">United States</small></div>
<div class="abs review boxed" style="left:791px"><div class="stars">★★★★★</div>“Tobias was incredibly responsive and the house was exactly what we thought it would be like. It was perfect to cook breakfasts and close to town. I would definitely recommend staying there.”<h4>Callum Reyes</h4><small>United States</small></div>

<!-- footer -->
<footer class="abs footer"></footer>
<h3 class="abs f-head" style="left:111px">USEFUL LINKS</h3>
<h3 class="abs f-head" style="left:321px">CONTACT INFORMATION</h3>
<h3 class="abs f-head" style="left:637px">GET IN TOUCH:</h3>
<ul class="abs links"><li>Home</li><li>About</li><li>Properties</li><li>Owner Login</li><li>Blogs</li><li>Contact</li></ul>
<div class="abs contact">
  <div class="row"><span class="ico"><svg width="14" height="18" viewBox="0 0 14 18"><path d="M7 1C3.7 1 1 3.6 1 6.9 1 11 7 17 7 17s6-6 6-10.1C13 3.6 10.3 1 7 1z" fill="none" stroke="#fff" stroke-width="1.6"/><circle cx="7" cy="7" r="2" fill="#fff"/></svg></span><span>Shop 2217B,Level 1 Harbourgate<br>Shopping Centre 87 Quillon Terrace<br>Southport</span></div>
  <div class="row"><span class="ico"><svg width="16" height="16" viewBox="0 0 16 16"><path d="M3 1l3 3-2 2c1 2 3 4 5 5l2-2 3 3-2 3C7 14 2 9 1 3z" fill="#fff"/></svg></span><span>Phone : +61 7 5500 1234</span></div>
  <div class="row"><span class="ico"><svg width="16" height="12" viewBox="0 0 16 12"><rect x="1" y="1" width="14" height="10" fill="#fff"/><path d="M1 1l7 6 7-6" stroke="#1f1f1f" stroke-width="1.4" fill="none"/></svg></span><span>Email : info@agentpivola.com</span></div>
</div>
<div class="abs field" style="left:639px;top:3485px;width:220px;height:32px">Name :</div>
<div class="abs field" style="left:868px;top:3485px;width:221px;height:32px;padding-left:40px">Phone :</div>
<div class="abs field" style="left:639px;top:3528px;width:450px;height:32px">Email :</div>
<div class="abs field" style="left:639px;top:3571px;width:450px;height:72px">Message :</div>
<div class="abs submit">SUBMIT</div>
<div class="abs rule"></div>
<p class="abs copyright">Copyrights © 2025 Agent Pivola. All Rights Reserved. &nbsp;| &nbsp;Privacy policy</p>
<div class="abs social"><i></i><i class="hl"></i><i></i><i></i></div>

</body>
</html>
```